Musician looking for catchy Web Design for promotion

My name is Brenna Coyle. I'm an Irish musician who plays the tin whistle and the flute. I'm also the leader of a traditional Irish music and dance ensemble called Gather the Willows (www.gatherthewillows-example.com) and for the past 30 years, I've toured the world performing thousands of concerts. I run an annual cruise (www.brennacoylevoyage-example.com) that I would like a link to, and I'm also I'm organizing tours to Ireland that I would like a page set up for. I'm looking for a website to promote my tours and my music.
Updates

Hello Graphic Designers, I am only looking for the design of the home page to make my decision. Thank you. Brenna

Target Market(s)

Music fans of Irlsh and World Music

Industry/Entity Type

Entertainment Industry

Number of Pages Required

5+ page

Requirements
Must have
• I'm looking for a catchy design that shows a photo of me. I would like a few links....
• BIO
• TOURDATES
• BRENNA COYLE CRUISE
• MUSICAL TOUR OF IRELAND
• CONTACT
• VIDEO
• GALLERY
• CONTACT
• MAILING LIST
• STORE
Nice to have
• we'll see!

```html
<!DOCTYPE html>
<html lang="en">
<head>
<meta charset="utf-8">
<title>Brenna Coyle — Musical Tour of Ireland</title>
<link href="https://fonts.googleapis.com/css2?family=Lato:wght@300;400;700&display=swap" rel="stylesheet">
<style>
:root{
  --orange:#f7931e;
  --gold:#fdb913;
  --ink:#333;
  --muted:#777;
  --light:#f7f7f7;
  --dark:#222325;
  --white:#fff;
}
*{margin:0;padding:0;box-sizing:border-box}
html,body{width:754px;height:1200px;overflow:hidden}
body{font-family:'Lato',sans-serif;color:var(--ink);background:var(--white);position:relative}
.abs{position:absolute}
/* header */
.header{top:0;left:0;width:754px;height:61px;background:var(--white)}
.brand{left:62px;top:16px;display:flex;align-items:center;gap:8px;color:#222;font-weight:700}
.brand-mark{width:26px;height:26px;border-radius:50%;background:#222}
.brand-name{font-size:10px;line-height:11px;letter-spacing:.3px}
.follow{right:62px;top:24px;display:flex;align-items:center;gap:7px;font-size:10px;color:#444}
.follow .sq{width:16px;height:16px;display:inline-block}
/* nav */
.nav{top:61px;left:0;width:754px;height:39px;background:var(--orange);display:flex;align-items:center;padding-left:62px}
.nav a{color:var(--white);text-decoration:none;font-size:7.4px;text-transform:uppercase;padding:0 6px;line-height:39px;position:relative}
.nav a+a::before{content:"|";position:absolute;left:-2px;opacity:.8}
.nav a.active{background:var(--gold);padding:0 8px}
/* hero */
.hero{top:100px;left:0;width:754px;height:303px;background:linear-gradient(100deg,#07090f 0%,#0f1522 45%,#2a2a33 65%,#6b5a4a 85%,#3a2e26 100%)}
.hero h1{position:absolute;left:0;width:484px;top:88px;text-align:center;font-weight:400;font-size:27px;color:var(--white);letter-spacing:.5px}
.hero p{position:absolute;left:0;width:484px;top:130px;text-align:center;font-size:13.5px;color:var(--white)}
.btn-ghost{position:absolute;top:170px;height:28px;border:2px solid var(--white);color:var(--white);font-size:9.5px;display:flex;align-items:center;justify-content:center}
.hero .arrow{position:absolute;top:136px}
/* welcome */
.welcome{top:403px;left:0;width:754px;height:101px;background:var(--light);text-align:center}
.welcome h2{font-weight:400;font-size:18px;color:#444;margin-top:20px}
.welcome p{font-size:7px;color:#777;line-height:13px;width:500px;margin:10px auto 0}
/* booking band */
.band{top:504px;left:0;width:754px;height:211px;background:linear-gradient(90deg,#2b1f1c,#3a2a25 40%,#2f2522 70%,#3b302c)}
.notch{top:504px;left:365px;width:0;height:0;border-left:13px solid transparent;border-right:13px solid transparent;border-top:13px solid var(--light)}
.video{left:88px;top:532px;width:299px;height:155px;border:2px solid var(--white);background:linear-gradient(135deg,#4a4035,#8a8070 50%,#3a332b)}
.play{position:absolute;left:127px;top:56px;width:40px;height:40px;border-radius:50%;background:rgba(255,255,255,.55)}
.form-title{left:428px;top:528px;font-size:11px;color:var(--white)}
.label{left:427px;font-size:9px;color:#aaa}
.field{left:427px;width:243px;height:24px;background:rgba(255,255,255,.22)}
.subscribe{left:427px;top:663px;width:243px;height:25px;background:linear-gradient(#fdb913,#f7931e);color:var(--white);font-size:10.5px;display:flex;align-items:center;justify-content:center}
/* blog */
.blog-title{top:734px;left:0;width:754px;text-align:center;font-size:16px;color:#444;font-weight:400}
.card{top:771px;width:199px}
.card .thumb{width:199px;height:130px;border:3px solid var(--white);box-shadow:0 0 3px rgba(0,0,0,.3)}
.card h3{font-weight:400;font-size:10px;color:#444;margin-top:16px}
.card p{font-size:7px;line-height:13px;color:#777;margin-top:6px;text-align:justify}
.card .meta{font-size:7px;color:#aaa;margin-top:6px}
.card .meta span{margin-right:14px}
/* footer */
.footer{top:1013px;left:0;width:754px;height:149px;background:var(--dark);color:var(--white)}
.footer h4{position:absolute;font-weight:400;font-size:14px}
.links{position:absolute;left:62px;top:56px;display:grid;grid-template-columns:84px 114px 80px;row-gap:10px}
.links span{font-size:7px;color:#bbb;padding-left:17px;position:relative;line-height:9px}
.links span::before{content:"»";position:absolute;left:0;color:var(--gold);font-size:9px;line-height:8px}
.touch{position:absolute;left:337px;top:52px;width:150px;font-size:7px;line-height:13px;color:#bbb}
.touch b{color:var(--gold);font-weight:400}
.touch div{margin-bottom:7px}
.news-text{position:absolute;left:535px;top:52px;width:150px;font-size:7px;line-height:13px;color:#bbb}
.news-input{position:absolute;left:535px;top:84px;width:113px;height:20px;background:#444}
.news-send{position:absolute;left:648px;top:84px;width:43px;height:20px;background:var(--gold);font-size:9.5px;display:flex;align-items:center;justify-content:center}
.circles{position:absolute;left:535px;top:115px;display:flex;gap:5px}
.circles i{width:15px;height:15px;border:1.5px solid var(--white);border-radius:50%}
.bottom{top:1162px;left:0;width:754px;height:38px;background:var(--gold);color:var(--white);font-size:7px;padding-left:62px;line-height:38px}
</style>
</head>
<body>

<header class="abs header">
  <div class="abs brand"><span class="brand-mark"></span><span class="brand-name">BRENNA COYLE'S<br>MUSICAL TOUR OF IRELAND</span></div>
  <div class="abs follow">Follow Us :
    <span class="sq" style="background:#3b5998"></span>
    <span class="sq" style="background:#2aa3ef"></span>
    <span class="sq" style="background:#f58220"></span>
    <span class="sq" style="background:#dd4b39"></span>
  </div>
</header>

<nav class="abs nav">
  <a class="active">Home</a><a>Bio</a><a>Tourdates</a><a>Brenna Coyle Cruise</a><a>Musical Tour of Ireland</a><a>Contact</a><a>Video</a><a>Gallery</a><a>Contact</a><a>Mailing List</a><a>Store</a>
</nav>

<section class="abs hero" role="img" aria-label="Photo of a musician playing a silver flute against a dark background">
  <h1>BRENNA COYLE</h1>
  <p>Irish musician who plays the tin whistle and the flute</p>
  <div class="btn-ghost" style="left:134px;width:101px">TAKE A TOUR</div>
  <div class="btn-ghost" style="left:248px;width:101px">LISTEN MY MUSIC</div>
  <svg class="arrow" style="left:26px" width="10" height="14" viewBox="0 0 10 14"><path d="M8 1L2 7l6 6" stroke="#fff" stroke-width="1.8" fill="none"/></svg>
  <svg class="arrow" style="left:718px" width="10" height="14" viewBox="0 0 10 14"><path d="M2 1l6 6-6 6" stroke="#fff" stroke-width="1.8" fill="none"/></svg>
</section>

<section class="abs welcome">
  <h2>Welcome to Willowmere</h2>
  <p>At vero eos et accusamus et iusto odio dignissimos ducimus qui blanditiis praesentium voluptatum deleniti atque corrupti quos dolores et quas molestias excepturi sint occaecati cupiditate non provident, similique sunt in culpa qui officia deserunt mollitia animi, id est laborum et dolorum fuga.</p>
</section>

<section class="abs band" role="img" aria-label="Dimmed background of musical instruments"></section>
<div class="abs notch"></div>
<div class="abs video" role="img" aria-label="Video still of the musician standing by an iron gate">
  <div class="play"><svg width="40" height="40" viewBox="0 0 40 40"><path d="M16 12l12 8-12 8z" fill="#333"/></svg></div>
</div>
<div class="abs form-title">All Other Booking Enquiries</div>
<div class="abs label" style="top:554px">Name</div>
<div class="abs field" style="top:570px"></div>
<div class="abs label" style="top:607px">Email</div>
<div class="abs field" style="top:623px"></div>
<div class="abs subscribe">Subscribe Now</div>

<h2 class="abs blog-title">Our Blog</h2>
<svg class="abs" style="left:26px;top:869px" width="12" height="24" viewBox="0 0 12 24"><path d="M11 1L1 12l10 11" stroke="#bbb" fill="none"/></svg>
<svg class="abs" style="left:714px;top:869px" width="12" height="24" viewBox="0 0 12 24"><path d="M1 1l10 11L1 23" stroke="#bbb" fill="none"/></svg>

<article class="abs card" style="left:62px">
  <div class="thumb" role="img" aria-label="Close-up of hands holding a tin whistle" style="background:linear-gradient(135deg,#5a2a14,#b5603a 50%,#3a1a0c)"></div>
  <h3>At vero eos et accusamus</h3>
  <p>Sed ut perspiciatis unde omnis iste natus error sit voluptatem accusantium doloremque laudantium, totam rem aperiam, eaque ipsa quae ab illo inventore. ....</p>
  <div class="meta"><span>Augest 1,2015</span><span>3 Comments</span></div>
</article>
<article class="abs card" style="left:276px">
  <div class="thumb" role="img" aria-label="The musician holding a whistle on a rocky seashore" style="background:linear-gradient(180deg,#c9d3da,#8c9a8a 50%,#6a6a5a)"></div>
  <h3>Sed ut perspiciatis unde</h3>
  <p>Sed ut perspiciatis unde omnis iste natus error sit voluptatem accusantium doloremque laudantium, totam rem aperiam, eaque ipsa quae ab illo inventore. ....</p>
  <div class="meta"><span>Augest 1,2015</span><span>3 Comments</span></div>
</article>
<article class="abs card" style="left:491px">
  <div class="thumb" role="img" aria-label="Orange walk of fame sign on a building" style="background:linear-gradient(135deg,#c8651a,#e8902e 50%,#a04a12)"></div>
  <h3>The standard Lorem Ipsum</h3>
  <p>Sed ut perspiciatis unde omnis iste natus error sit voluptatem accusantium doloremque laudantium, totam rem aperiam, eaque ipsa quae ab illo inventore. ....</p>
  <div class="meta"><span>Augest 1,2015</span><span>3 Comments</span></div>
</article>

<footer class="abs footer">
  <h4 style="left:62px;top:26px">Quick Links</h4>
  <div class="links">
    <span>Home</span><span>Musical Tour Of Ireland</span><span>Contact</span>
    <span>Bio</span><span>Contact</span><span>Mailing List</span>
    <span>Tourdates</span><span>Video</span><span>Store</span>
    <span>Brenna</span><span>Gallery</span><span></span>
  </div>
  <h4 style="left:335px;top:28px">Get In Touch</h4>
  <div class="touch">
    <div><b>Address :</b> 200 Latin words, combined with a handful of model sentence structures</div>
    <div><b>Phone No :</b> (088) - 555010234</div>
    <div><b>Mail Id :</b> info@harbourlane-example.com</div>
  </div>
  <h4 style="left:535px;top:28px">NewsLetter</h4>
  <div class="news-text">There are many variations of passages of Lorem Ipsum available, but the majority</div>
  <div class="news-input"></div>
  <div class="news-send">Send</div>
  <div class="circles"><i></i><i></i><i></i></div>
</footer>

<div class="abs bottom">Copyrights@2016 Company Name . all rights reserved</div>

</body>
</html>
```